Wedding Videography Wordpress Website Theme

We need a modern and high-end website look for our wedding video and film business. We film weddings all over the United Kingdom and at European destinations so need something to reflect our work. The website should be visually stunning with images and videos being the focal point as this is what our services are.

The current website is www.brunolessway.com so you will be able to see our brand.

My Social is www.instagram.com/brunolesswayfilms so a new design should link in with this idea.

We need the following pages designed by the winning designer

1 - Homepage
2 - Films Index Page
3 - Testimonials
4 - Prices
5 - Reviews
6 - Meet Bruno (About)
7 - Contact
8 - Blog Index
9 - Blog Page

All pages must be consistent so have a similar style.

Pages on menu:
Meet Bruno
Videos
Packages
Testimionials
Journal (Blog)
Contact

We require a responsive look too. Over 90% of our visitors access the website via their mobile devices.

```html
<!DOCTYPE html>
<html lang="en">
<head>
<meta charset="utf-8">
<title>Meet Bruno – Bruno Lessway Wedding Films</title>
<link rel="stylesheet" href="https://fonts.googleapis.com/css2?family=Cinzel:wght@400;500&family=Jost:wght@300;400;500&display=swap">
<style>
:root{
  --gold:#b0955b;
  --gold-soft:#c8b07b;
  --sand:#e3d6b1;
  --cream:#f4ede0;
  --ink:#2c2a28;
  --text:#5b5752;
  --muted:#8a857e;
  --dark:#17110e;
  --line:#e5e0d8;
  --white:#ffffff;
  --serif:'Cinzel', 'Times New Roman', serif;
  --sans:'Jost', 'Helvetica Neue', Arial, sans-serif;
}
*{margin:0;padding:0;box-sizing:border-box}
html,body{width:1200px;height:2506px;overflow:hidden;background:var(--white)}
body{font-family:var(--sans);color:var(--text)}
.artboard{position:relative;width:1200px;height:2506px;overflow:hidden;background:var(--white)}
.abs{position:absolute}
.photo{position:absolute}
.title-lettering{left:97px;top:44px;width:63px;height:292px;background:linear-gradient(180deg,#d8d8d8,#cfcfcf);border-radius:4px}

/* ---------- desktop ---------- */
.desktop{position:absolute;left:211px;top:2px;width:645px;height:2504px;background:var(--white);box-shadow:0 0 0 1px #f0ede8}
.desktop section{position:absolute;left:0;width:645px}

.hero{top:0;height:331px}
.hero .photo{inset:0;background:linear-gradient(180deg,#6f6d6c 0%,#7d7a78 45%,#6f725f 70%,#59603f 100%)}
.brand{position:absolute;font-family:var(--serif);letter-spacing:.18em;white-space:nowrap}
.hero .brand{left:64px;top:40px;color:var(--white);font-size:10px}
.nav{position:absolute;top:44px;left:212px;font-size:6.4px;letter-spacing:.05em;color:var(--white);font-weight:500}
.nav a{position:absolute;white-space:nowrap;text-decoration:none;color:inherit}
.nav .current::after{content:"";position:absolute;left:0;top:11px;width:9px;height:1.5px;background:var(--gold-soft)}
.btn-enquire{position:absolute;left:505px;top:36px;width:78px;height:23px;background:var(--sand);color:var(--ink);font-size:6.4px;font-weight:500;letter-spacing:.05em;display:flex;align-items:center;justify-content:center}
.hero-title{position:absolute;left:0;right:0;top:162px;text-align:center;font-family:var(--serif);font-weight:400;color:var(--gold-soft);font-size:17px;letter-spacing:.04em}
.hero-sub{position:absolute;left:0;right:0;top:192px;text-align:center;color:var(--white);font-size:8.4px;letter-spacing:.02em}

.section-title{position:absolute;left:0;right:0;text-align:center;font-family:var(--serif);font-weight:400;color:var(--gold);letter-spacing:.05em}

.intro{top:331px;height:407px}
.intro .section-title{top:22px;font-size:13px}
.intro .photo{left:62px;top:74px;width:233px;height:288px;background:linear-gradient(160deg,#4d5a3c 0%,#8d8a78 35%,#c9b9a2 60%,#3a3029 100%)}
.intro-row{position:absolute;left:331px;width:247px}
.icon-disc{position:absolute;border-radius:50%;background:var(--cream);display:flex;align-items:center;justify-content:center}
.intro-row .icon-disc{left:0;width:46px;height:46px}
.intro-row p{position:absolute;left:64px;width:180px;font-size:7.2px;line-height:14.2px;color:var(--text)}
.intro-row .rule{position:absolute;left:0;width:254px;height:1px;background:var(--line)}

.testimonial{top:736px;height:280px;background:var(--dark)}
.testimonial .photo{left:280px;top:0;width:365px;height:280px;background:linear-gradient(90deg,var(--dark) 0%,#3a2f27 25%,#6d655d 55%,#8a8378 80%,#5a524a 100%)}
.testimonial h2{position:absolute;left:62px;top:53px;width:270px;font-family:var(--serif);font-weight:400;color:var(--gold-soft);font-size:12px;line-height:20px;letter-spacing:.02em}
.testimonial .quote-mark{position:absolute;left:60px;top:118px;font-family:var(--serif);font-size:40px;color:#3b332c;line-height:1}
.testimonial p{position:absolute;left:62px;top:137px;width:212px;font-size:7.2px;line-height:14.6px;color:#ebe5dc}

.experience{top:1016px;height:291px}
.experience .photo-a{left:62px;top:42px;width:235px;height:108px;background:linear-gradient(180deg,#8a8e8a 0%,#5e7a45 45%,#4f6a38 100%)}
.experience .photo-b{left:61px;top:167px;width:127px;height:108px;background:linear-gradient(180deg,#a38e63 0%,#c2a36d 50%,#a8874f 100%)}
.years-box{position:absolute;left:200px;top:167px;width:97px;height:108px;border:5px solid var(--sand);background:var(--white);text-align:center}
.years-box .num{font-family:var(--serif);font-size:32px;color:var(--ink);margin-top:14px;line-height:1}
.years-box .label{font-size:9.4px;color:var(--muted);line-height:12px;margin-top:6px}
.experience .brand{left:339px;width:239px;top:98px;text-align:center;color:var(--gold);font-size:12.5px}
.experience .lede{position:absolute;left:339px;top:144px;width:239px;text-align:center;font-size:9.4px;line-height:24px;color:var(--ink)}

.mission{top:1307px;height:486px}
.mission .photo{left:63px;top:16px;width:521px;height:233px;background:linear-gradient(90deg,#b57a55 0%,#5b554a 35%,#3c3b36 55%,#a7a39a 80%,#c79c82 100%)}
.mission .section-title{top:278px;font-size:13px}
.mission-item{position:absolute;top:321px;width:145px}
.mission-item svg{position:absolute;left:0;top:1px}
.mission-item p{position:absolute;left:24px;width:122px;font-size:7.2px;line-height:14.2px;color:var(--text)}
.mission-item .dash{position:absolute;left:24px;width:16px;height:1.5px;background:var(--gold-soft)}

.family{top:1793px;height:299px}
.family .photo{inset:0;background:linear-gradient(135deg,#8e3c2a 0%,#c86a4b 30%,#a8553c 55%,#e0c8b8 75%,#8a3a2a 100%)}
.family h2{position:absolute;left:0;right:0;top:107px;text-align:center;font-family:var(--serif);font-weight:400;color:var(--white);font-size:20px;letter-spacing:.03em}
.play{position:absolute;left:307px;top:149px;width:24px;height:24px;border-radius:50%;background:rgba(255,255,255,.7);border:1.5px solid rgba(255,255,255,.9)}

.social-feed{top:2092px;height:251px;background:var(--sand)}
.social-feed .section-title{top:36px;font-size:14px;letter-spacing:.28em;color:#7a6a45}
.feed-grid{position:absolute;left:62px;top:78px;display:flex;gap:11px}
.feed-grid div{width:78px;height:86px}
.btn-follow{position:absolute;left:254px;top:192px;width:138px;height:29px;background:var(--white);font-size:7.4px;color:var(--ink);display:flex;align-items:center;justify-content:center}

.footer{top:2343px;height:161px}
.footer .brand{left:62px;top:60px;width:100px;text-align:center;color:var(--gold);font-size:9.5px}
.social{position:absolute;display:flex;gap:7px}
.social span{display:block;border:1px solid var(--gold-soft);border-radius:3px}
.footer .social{left:82px;top:101px}
.footer .social span{width:12px;height:12px}
.foot-head{position:absolute;font-size:8.6px;color:var(--ink);font-weight:500}
.foot-head::after{content:"";display:inline-block;width:12px;height:1px;background:var(--muted);margin-left:5px;vertical-align:middle}
.foot-line{position:absolute;font-size:7.2px;color:var(--text);white-space:nowrap}
.copyright{position:absolute;left:0;right:0;top:140px;text-align:center;font-size:5.6px;color:var(--muted)}

/* ---------- mobile ---------- */
.mobile{position:absolute;left:949px;top:1px;width:120px;height:2505px;background:var(--white);box-shadow:0 0 0 1px #f0ede8}
.m{position:absolute;left:0;width:120px}
.m-hero{top:0;height:186px}
.m-hero .photo{inset:0;background:linear-gradient(180deg,#6f6d6c 0%,#7d7a78 55%,#6c6f5e 100%)}
.m-hero .brand{left:5px;top:20px;color:var(--white);font-size:4.6px}
.burger{position:absolute;right:8px;top:19px;width:8px}
.burger i{display:block;height:1px;background:var(--white);margin-bottom:1.6px}
.m-hero h1{position:absolute;left:0;right:0;top:89px;text-align:center;font-family:var(--serif);font-weight:400;color:var(--gold-soft);font-size:11px}
.m-hero p{position:absolute;left:18px;right:18px;top:110px;text-align:center;color:var(--white);font-size:4.8px;line-height:11.6px;font-weight:500}
.m-title{position:absolute;left:0;right:0;text-align:center;font-family:var(--serif);color:var(--gold);font-size:9px;letter-spacing:.04em}
.m-text{position:absolute;left:8px;width:104px;text-align:center;font-size:4.4px;line-height:9.8px;color:var(--text)}
.m-rule{position:absolute;left:6px;width:108px;height:1px;background:var(--line)}
.m .icon-disc{left:43px;width:33px;height:33px}
.m-mission-item{position:absolute;left:9px;width:106px}
.m-mission-item svg{position:absolute;left:0;top:0}
.m-mission-item p{position:absolute;left:13px;width:92px;font-size:4.3px;line-height:9.8px;color:var(--text)}
.m-mission-item .dash{position:absolute;left:13px;width:10px;height:1px;background:var(--gold-soft)}
</style>
</head>
<body>
<div class="artboard">

  <div class="abs title-lettering" role="img" aria-label="Hand-lettered page title reading Meet Bruno"></div>

  <!-- ===== Desktop page ===== -->
  <div class="desktop">

    <section class="hero">
      <div class="photo" role="img" aria-label="Bride and groom walking arm in arm on a grassy hilltop under a grey sky"></div>
      <div class="brand">BRUNO LESSWAY</div>
      <nav class="nav">
        <a class="current" style="left:0">MEET BRUNO</a>
        <a style="left:62px">VIDEOS</a>
        <a style="left:109px">PACKAGES</a>
        <a style="left:169px">TESTIMONIALS</a>
        <a style="left:238px">JOURNAL</a>
      </nav>
      <div class="btn-enquire">ENQUIRE</div>
      <h1 class="hero-title">MEET BRUNO</h1>
      <p class="hero-sub">North East and Yorkshire Wedding Videographer</p>
    </section>

    <section class="intro">
      <h2 class="section-title">MEET BRUNO</h2>
      <div class="photo" role="img" aria-label="Bruno showing footage on his camera to a smiling bride and groom"></div>

      <div class="intro-row" style="top:78px">
        <div class="icon-disc">
          <svg width="24" height="22" viewBox="0 0 24 22" fill="none" stroke="#2c2a28" stroke-width="1.3"><path d="M3 3h18v11H10l-5 5v-5H3z"/><path d="M7 7h10M7 10h7"/></svg>
        </div>
        <p>Thanks so much for exploring my website. I hope you've had a chance to watch some of the gorgeous wedding films and you've enjoyed seeing the kind of high-quality, professional wedding video you could expect too.</p>
        <div class="rule" style="top:78px"></div>
      </div>

      <div class="intro-row" style="top:181px">
        <div class="icon-disc">
          <svg width="24" height="20" viewBox="0 0 24 20" fill="none" stroke="#2c2a28" stroke-width="1.3"><circle cx="6" cy="5" r="3"/><circle cx="13" cy="5" r="3"/><rect x="2" y="9" width="14" height="9" rx="1"/><path d="M16 12l6-3v9l-6-3"/></svg>
        </div>
        <p style="top:-3px">Videomaking has been a passion since I was eight years old. From making family videos, I went on to study video at college and then at degree level. You could say it's second nature to me by now – I've been honing my filmmaking skills for years!</p>
        <div class="rule" style="top:79px"></div>
      </div>

      <div class="intro-row" style="top:283px">
        <div class="icon-disc">
          <svg width="22" height="20" viewBox="0 0 22 20" fill="none" stroke="#2c2a28" stroke-width="1.3"><path d="M11 9C9 5 4 6 5 10c1 3 6 6 6 6s5-3 6-6c1-4-4-5-6-1z"/><path d="M2 11l4 6h10l4-6"/></svg>
        </div>
        <p style="top:-4px">When I'm not behind a camera, I love spending quality time with my two children (have you seen our family videos here?). We're usually on an adventure somewhere, having fun. Life's for making memories, right? And making sure we never forget the little details.</p>
        <div class="rule" style="top:79px"></div>
      </div>
    </section>

    <section class="testimonial">
      <div class="photo" role="img" aria-label="Groom holding the bride's hands during a church ceremony"></div>
      <h2>CREATING BESPOKE,<br>CINEMATIC WEDDING VIDEOS<br>TO CHERISH FOREVER</h2>
      <div class="quote-mark">“</div>
      <p>One of the best decisions we made was choosing you guys to film our wedding! It's absolutely fantastic, it has everyone so emotional watching it, we can't thank you enough for capturing our special day! You were amazing from start to finish. Thanks so much.” Laura and Daniel</p>
    </section>

    <section class="experience">
      <div class="photo photo-a" role="img" aria-label="Outdoor wedding ceremony aisle with guests seated either side of a gazebo"></div>
      <div class="photo photo-b" role="img" aria-label="Bride and groom embracing in a golden wheat field"></div>
      <div class="years-box"><div class="num">25</div><div class="label">Years of<br>Experience</div></div>
      <div class="brand">BRUNO LESSWAY</div>
      <p class="lede">With 25 years of video production and media industry experience, incredible testimonials, a calm persona, and the ability to blend into the background when necessary, you can rest assured you're in safe hands.</p>
    </section>

    <section class="mission">
      <div class="photo" role="img" aria-label="Selfie of Bruno with his two children outdoors"></div>
      <h2 class="section-title">MY WEDDING FILMMAKING MISSION</h2>

      <div class="mission-item" style="left:62px">
        <svg width="14" height="12" viewBox="0 0 14 12" fill="none" stroke="#b0955b" stroke-width="1.6"><path d="M1 6l4 4 8-9"/></svg>
        <p>“On the day Bruno and Owen were great in making us feel comfortable and we hardly realised they were there or filming most of the time which was perfect as we wanted to capture those kinds of moments where people don't realise they are being filmed that we may miss.” Emma and Jordan.</p>
        <div class="dash" style="top:148px"></div>
      </div>
      <div class="mission-item" style="left:248px">
        <svg width="14" height="12" viewBox="0 0 14 12" fill="none" stroke="#b0955b" stroke-width="1.6"><path d="M1 6l4 4 8-9"/></svg>
        <p>Ultimately, my mission is to put the wedding party at ease so I can create a stunning wedding video, filled with timeless memories you can't stop sharing. I do this by focusing on your day's unique atmosphere and the subtle moments that could easily be forgotten over time.</p>
        <div class="dash" style="top:120px"></div>
      </div>
      <div class="mission-item" style="left:438px">
        <svg width="14" height="12" viewBox="0 0 14 12" fill="none" stroke="#b0955b" stroke-width="1.6"><path d="M1 6l4 4 8-9"/></svg>
        <p>And I don't just capture the moving pictures. I ensure the sounds are filmed too: the vows, the readings, the speeches, the laughter – everything that transports you back to the day in a heartbeat.</p>
        <div class="dash" style="top:92px"></div>
      </div>
    </section>

    <section class="family">
      <div class="photo" role="img" aria-label="Two children laughing on a striped deckchair at a fairground"></div>
      <h2>FAMILY TIME</h2>
      <div class="play">
        <svg width="21" height="21" viewBox="0 0 21 21"><path d="M8.5 6.5l6 4-6 4z" fill="#6b6b6b"/></svg>
      </div>
    </section>

    <section class="social-feed">
      <h2 class="section-title">FOLLOW ME ON SOCIAL</h2>
      <div class="feed-grid">
        <div role="img" aria-label="Couple on a cobbled street" style="background:linear-gradient(180deg,#8c8880,#4c4944)"></div>
        <div role="img" aria-label="Couple under falling confetti" style="background:linear-gradient(180deg,#5d6470,#b7aba0)"></div>
        <div role="img" aria-label="Horse-drawn carriage in a field" style="background:linear-gradient(180deg,#c7c8c4,#8a9368)"></div>
        <div role="img" aria-label="Groom and bride at the altar" style="background:linear-gradient(180deg,#3b3834,#a8a39b)"></div>
        <div role="img" aria-label="Couple laughing together" style="background:linear-gradient(180deg,#2f2d2a,#c1a994)"></div>
        <div role="img" aria-label="Wedding guests jumping on a lawn" style="background:linear-gradient(180deg,#9ba7b2,#6e8048)"></div>
      </div>
      <div class="btn-follow">Follow me @brunolesswayfilms</div>
    </section>

    <section class="footer">
      <div class="brand">BRUNO LESSWAY</div>
      <div class="social"><span></span><span></span><span></span></div>
      <div class="foot-head" style="left:222px;top:45px">Contact</div>
      <svg class="abs" style="left:222px;top:71px" width="9" height="9" viewBox="0 0 10 10" fill="none" stroke="#8a857e" stroke-width="1"><path d="M2 1l2 0 1 2.5-1.2 1a6 6 0 002.7 2.7l1-1.2L10 8v2C5 10 0 5 0 1z"/></svg>
      <div class="foot-line" style="left:242px;top:71px">07700 900 418</div>
      <svg class="abs" style="left:222px;top:97px" width="9" height="8" viewBox="0 0 10 8" fill="none" stroke="#8a857e" stroke-width="1"><rect x=".5" y=".5" width="9" height="7"/><path d="M.5 .5L5 4.5 9.5 .5"/></svg>
      <div class="foot-line" style="left:242px;top:97px">films@brunolessway.com</div>
      <div class="foot-head" style="left:377px;top:45px">Links</div>
      <div class="foot-line" style="left:378px;top:69px">FAQ's</div>
      <div class="foot-line" style="left:378px;top:87px">Wedding Photography</div>
      <div class="foot-line" style="left:378px;top:105px">Commercial</div>
      <div class="foot-line" style="left:495px;top:69px">North East Wedding Venues</div>
      <div class="foot-line" style="left:495px;top:87px">Free Speeches Guide</div>
      <div class="foot-line" style="left:495px;top:105px">Blog</div>
      <p class="copyright">© Copyright 2022 Bruno Lessway Films Ltd All Rights Reserved</p>
    </section>
  </div>

  <!-- ===== Mobile page ===== -->
  <div class="mobile">
    <div class="m m-hero">
      <div class="photo" role="img" aria-label="Bride and groom walking arm in arm on a hilltop"></div>
      <div class="brand">BRUNO LESSWAY</div>
      <div class="burger"><i></i><i style="width:6px"></i><i></i></div>
      <h1>MEET BRUNO</h1>
      <p>NORTH EAST AND YORKSHIRE WEDDING VIDEOGRAPHER</p>
    </div>

    <div class="m-title" style="top:198px">MEET BRUNO</div>
    <div class="photo" role="img" aria-label="Bruno showing camera footage to a bride and groom" style="left:1px;top:218px;width:118px;height:108px;background:linear-gradient(160deg,#4d5a3c,#c9b9a2 60%,#3a3029)"></div>

    <div class="m" style="top:0">
      <div class="icon-disc" style="top:336px"><svg width="16" height="14" viewBox="0 0 24 22" fill="none" stroke="#2c2a28" stroke-width="1.6"><path d="M3 3h18v11H10l-5 5v-5H3z"/></svg></div>
      <p class="m-text" style="top:374px">Thanks so much for exploring my website. I hope you've had a chance to watch some of the gorgeous wedding films and you've enjoyed seeing the kind of high-quality, professional wedding video you could expect too.</p>
      <div class="m-rule" style="top:443px"></div>
      <div class="icon-disc" style="top:451px"><svg width="16" height="14" viewBox="0 0 24 20" fill="none" stroke="#2c2a28" stroke-width="1.6"><circle cx="6" cy="5" r="3"/><circle cx="13" cy="5" r="3"/><rect x="2" y="9" width="14" height="9" rx="1"/><path d="M16 12l6-3v9l-6-3"/></svg></div>
      <p class="m-text" style="top:487px">Videomaking has been a passion since I was eight years old. From making family videos, I went on to study video at college and then at degree level. You could say it's second nature to me by now – I've been honing my filmmaking skills for years!</p>
      <div class="m-rule" style="top:557px"></div>
      <div class="icon-disc" style="top:569px"><svg width="15" height="14" viewBox="0 0 22 20" fill="none" stroke="#2c2a28" stroke-width="1.6"><path d="M11 9C9 5 4 6 5 10c1 3 6 6 6 6s5-3 6-6c1-4-4-5-6-1z"/></svg></div>
      <p class="m-text" style="top:609px">When I'm not behind a camera, I love spending quality time with my two children (have you seen our family videos here?). We're usually on an adventure somewhere, having fun. Life's for making memories, right? And making sure we never forget the little details.</p>
    </div>

    <div class="m" style="top:699px;height:303px;background:var(--dark)">
      <p class="abs" style="left:8px;top:21px;width:104px;text-align:center;font-family:var(--serif);color:var(--gold-soft);font-size:7.2px;line-height:14px">CREATING BESPOKE, CINEMATIC WEDDING VIDEOS TO CHERISH FOREVER</p>
      <p class="abs" style="left:7px;top:92px;width:106px;text-align:center;font-size:4.4px;line-height:9.8px;color:#ebe5dc">One of the best decisions we made was choosing you guys to film our wedding! It's absolutely fantastic, it has everyone so emotional watching it, we can't thank you enough for capturing our special day! You were amazing from start to finish. Thanks so much.” Laura and Daniel</p>
      <div class="photo" role="img" aria-label="Groom holding the bride's hands in church" style="left:0;top:172px;width:120px;height:131px;background:linear-gradient(180deg,var(--dark),#6d655d 40%,#8a8378)"></div>
    </div>

    <div class="photo" role="img" aria-label="Outdoor wedding ceremony aisle with guests" style="left:1px;top:1004px;width:118px;height:74px;background:linear-gradient(180deg,#8a8e8a,#4f6a38)"></div>
    <div class="photo" role="img" aria-label="Couple in a wheat field" style="left:1px;top:1082px;width:61px;height:76px;background:linear-gradient(180deg,#a38e63,#a8874f)"></div>
    <div class="abs" style="left:65px;top:1081px;width:55px;height:77px;border:3px solid var(--sand);text-align:center">
      <div style="font-family:var(--serif);font-size:21px;color:var(--ink);margin-top:10px;line-height:1">25</div>
      <div style="font-size:6px;color:var(--muted);line-height:8px;margin-top:5px">Years of<br>Experience</div>
    </div>

    <div class="brand" style="left:0;width:120px;top:1203px;text-align:center;color:var(--gold);font-size:7px">BRUNO LESSWAY</div>
    <p class="abs" style="left:6px;top:1231px;width:108px;text-align:center;font-size:5.6px;line-height:17px;color:var(--ink)">With 25 years of video production and media industry experience, incredible testimonials, a calm persona, and the ability to blend into the background when necessary, you can rest assured you're in safe hands.</p>

    <div class="photo" role="img" aria-label="Selfie of Bruno with his two children" style="left:0;top:1364px;width:120px;height:73px;background:linear-gradient(90deg,#b57a55,#3c3b36 45%,#a7a39a 80%,#c79c82)"></div>
    <p class="m-title" style="top:1448px;font-size:7.6px;line-height:14px;left:8px;right:8px">MY WEDDING FILMMAKING MISSION</p>

    <div class="m-mission-item" style="top:1487px">
      <svg width="8" height="7" viewBox="0 0 14 12" fill="none" stroke="#b0955b" stroke-width="2"><path d="M1 6l4 4 8-9"/></svg>
      <p>“On the day Bruno and Owen were great in making us feel comfortable and we hardly realised they were there or filming most of the time which was perfect as we wanted to capture those kinds of moments where people don't realise they are being filmed that we may miss.” Emma and Jordan.</p>
      <div class="dash" style="top:93px"></div>
    </div>
    <div class="m-mission-item" style="top:1595px">
      <svg width="8" height="7" viewBox="0 0 14 12" fill="none" stroke="#b0955b" stroke-width="2"><path d="M1 6l4 4 8-9"/></svg>
      <p>Ultimately, my mission is to put the wedding party at ease so I can create a stunning wedding video, filled with timeless memories you can't stop sharing. I do this by focusing on your day's unique atmosphere and the subtle moments that could easily be forgotten over time.</p>
      <div class="dash" style="top:84px"></div>
    </div>
    <div class="m-mission-item" style="top:1692px">
      <svg width="8" height="7" viewBox="0 0 14 12" fill="none" stroke="#b0955b" stroke-width="2"><path d="M1 6l4 4 8-9"/></svg>
      <p>And I don't just capture the moving pictures. I ensure the sounds are filmed too: the vows, the readings, the speeches, the laughter – everything that transports you back to the day in a heartbeat.</p>
    </div>

    <div class="m" style="top:1773px;height:173px">
      <div class="photo" role="img" aria-label="Children laughing on a striped deckchair" style="inset:0;background:linear-gradient(135deg,#8e3c2a,#c86a4b 35%,#e0c8b8 70%,#8a3a2a)"></div>
      <p class="abs" style="left:0;right:0;top:62px;text-align:center;font-family:var(--serif);color:var(--white);font-size:11px">FAMILY TIME</p>
      <div class="abs" style="left:51px;top:88px;width:16px;height:16px;border-radius:50%;background:rgba(255,255,255,.7)"><svg width="16" height="16" viewBox="0 0 21 21"><path d="M8.5 6.5l6 4-6 4z" fill="#6b6b6b"/></svg></div>
    </div>

    <div class="m" style="top:1946px;height:277px;background:var(--cream)">
      <p class="abs" style="left:0;right:0;top:17px;text-align:center;font-family:var(--serif);color:#7a6a45;font-size:7px;letter-spacing:.25em;line-height:13px">FOLLOW ME ON<br>SOCIAL</p>
      <div class="photo" role="img" aria-label="Couple on a cobbled street" style="left:3px;top:54px;width:56px;height:55px;background:linear-gradient(180deg,#8c8880,#4c4944)"></div>
      <div class="photo" role="img" aria-label="Couple under confetti" style="left:61px;top:54px;width:56px;height:55px;background:linear-gradient(180deg,#5d6470,#b7aba0)"></div>
      <div class="photo" role="img" aria-label="Horse-drawn carriage" style="left:3px;top:114px;width:56px;height:55px;background:linear-gradient(180deg,#c7c8c4,#8a9368)"></div>
      <div class="photo" role="img" aria-label="Couple at the altar" style="left:61px;top:114px;width:56px;height:55px;background:linear-gradient(180deg,#3b3834,#a8a39b)"></div>
      <div class="photo" role="img" aria-label="Couple laughing" style="left:3px;top:174px;width:56px;height:56px;background:linear-gradient(180deg,#2f2d2a,#c1a994)"></div>
      <div class="photo" role="img" aria-label="Guests jumping on a lawn" style="left:61px;top:174px;width:56px;height:56px;background:linear-gradient(180deg,#9ba7b2,#6e8048)"></div>
      <div class="abs" style="left:12px;top:242px;width:96px;height:21px;background:var(--white);font-size:4.6px;color:var(--ink);display:flex;align-items:center;justify-content:center">Follow me @brunolesswayfilms</div>
    </div>

    <div class="m" style="top:2223px;height:282px">
      <div class="brand" style="left:0;width:120px;top:28px;text-align:center;color:var(--gold);font-size:5.8px">BRUNO LESSWAY</div>
      <div class="social" style="left:41px;top:58px;gap:5px"><span style="width:9px;height:9px"></span><span style="width:9px;height:9px"></span><span style="width:9px;height:9px"></span></div>
      <div class="foot-head" style="left:15px;top:92px;font-size:5.4px">Contact</div>
      <div class="foot-line" style="left:30px;top:110px;font-size:4.4px">07700 900 418</div>
      <div class="foot-line" style="left:30px;top:129px;font-size:4.4px">films@brunolessway.com</div>
      <svg class="abs" style="left:15px;top:110px" width="6" height="6" viewBox="0 0 10 10" fill="none" stroke="#8a857e" stroke-width="1.2"><path d="M2 1l2 0 1 2.5-1.2 1a6 6 0 002.7 2.7l1-1.2L10 8v2C5 10 0 5 0 1z"/></svg>
      <svg class="abs" style="left:15px;top:129px" width="6" height="5" viewBox="0 0 10 8" fill="none" stroke="#8a857e" stroke-width="1.2"><rect x=".5" y=".5" width="9" height="7"/><path d="M.5 .5L5 4.5 9.5 .5"/></svg>
      <div class="foot-head" style="left:15px;top:150px;font-size:5.4px">Links</div>
      <div class="foot-line" style="left:17px;top:165px;font-size:4px">FAQ's</div>
      <div class="foot-line" style="left:17px;top:178px;font-size:4px">Wedding Photography</div>
      <div class="foot-line" style="left:17px;top:191px;font-size:4px">Commercial</div>
      <div class="foot-line" style="left:17px;top:204px;font-size:4px">North East Wedding Venues</div>
      <div class="foot-line" style="left:17px;top:217px;font-size:4px">Free Speeches Guide</div>
      <div class="foot-line" style="left:17px;top:230px;font-size:4px">Blog</div>
      <p class="abs" style="left:17px;top:250px;width:90px;font-size:3.6px;line-height:7px;color:var(--muted)">© Copyright 2022 Bruno Lessway Films Ltd<br>All Rights Reserved</p>
    </div>
  </div>

</div>
</body>
</html>
```